Pelican HVAC WordPress website design

Design a new modern, clean, website for HVAC mechanical business that uses company logo/colors for branding and recognition. Files attached are just for band and color information. Here is a website design that appeals to me https://www.corvellsupply.example/

A clear description of who we are and what we do

An easily-navigated site map

An easily-navigated site map for mobile devices

Easy-to-find contact information

Obvious call to action for service, installs or to schedule estimates

about us page

Provide a way for potential customers to contact us via text or email

provide a way that allows a customer to upload a picture to request a service call or quote.
Updates

I'm looking for the design to be completed in WordPress

Industry/Entity Type

HVAC Mechanical & Building Automation / Controls contractor

Coding

Coded - Design and coding required

Number of Pages Required

5+ page

Colors
0054AA
0677BA
7BADD7
CADEEF
E8F1F8

Requirements
Must have
• Design a new modern, clean, website for HVAC mechanical business that uses company logo/colors for branding and recognition. Files attached are just for band and color information. Here is a website design that appeals to me https://www.corvellsupply.example/ A clear description of who we are and what we do An easily-navigated site map An easily-navigated site map for mobile devices Easy-to-find contact information Obvious call to action for service, installs or to schedule estimates about us page Provide a way for potential customers to contact us via text or email provide a way that allows a customer to upload a picture to request a service call or quote.
Nice to have

```html
<!DOCTYPE html>
<html lang="en">
<head>
<meta charset="utf-8">
<title>Pelican HVAC</title>
<link href="https://fonts.googleapis.com/css2?family=Open+Sans:wght@400;500;600;700&display=swap" rel="stylesheet">
<style>
:root{
  --navy:#072f6b;
  --blue:#0054aa;
  --mid:#0677ba;
  --sky:#7badd7;
  --pale:#cadeef;
  --mist:#e8f1f8;
  --ink:#222;
  --text:#3a3a3a;
  --band:#c9cfdb;
  --black:#000;
}
*{box-sizing:border-box;margin:0;padding:0}
html,body{width:1200px;height:3937px;overflow:hidden}
body{font-family:"Open Sans",sans-serif;color:var(--ink);background:#fff;position:relative}
.abs{position:absolute}
.btn{position:absolute;display:flex;align-items:center;justify-content:center;background:var(--navy);color:#fff;border-radius:20px;font-weight:600;font-size:15px;box-shadow:-3px 2px 0 var(--mid)}
/* header */
.topbar{left:443px;top:0;width:757px;height:46px;background:var(--blue);clip-path:polygon(0 0,100% 0,100% 100%,40px 100%);color:#fff;font-size:13.5px}
.topbar span{position:absolute;top:14px;display:flex;align-items:center;gap:10px}
.ico{width:24px;height:24px;border-radius:50%;background:#fff;display:inline-flex;align-items:center;justify-content:center}
.nav{left:485px;top:66px;font-size:15px;font-weight:500;color:#111}
.nav a{position:absolute;white-space:nowrap;color:inherit;text-decoration:none}
.brand{display:flex;align-items:center;gap:14px;font-weight:700;font-size:34px;color:var(--navy)}
.brand i{width:40px;height:40px;border-radius:50%;background:var(--blue);display:block}
/* hero */
.hero{left:0;top:102px;width:1200px;height:536px;background:linear-gradient(90deg,#4c5a66 0%,#7a8994 45%,#5f7fa8 75%,#8e9aa8 100%)}
.hero-tint{left:0;top:102px;width:1200px;height:536px;background:linear-gradient(90deg,rgba(20,30,45,.5),rgba(20,30,45,0) 60%)}
.welcome{left:110px;top:276px;color:#fff;font-size:20px}
.hero h1{position:absolute;left:110px;top:318px;color:#fff;font-size:52px;font-weight:700;white-space:nowrap}
/* about */
.frame{left:130px;top:755px;width:364px;height:353px;background:var(--blue);clip-path:polygon(0 0,100% 92%,100% 100%,0 100%)}
.frame2{left:130px;top:1085px;width:364px;height:23px;background:var(--blue);clip-path:polygon(0 0,88% 0,100% 100%,0 100%)}
.aboutphoto{left:151px;top:723px;width:407px;height:362px;background:linear-gradient(135deg,#9aa6b2,#c9d2da 55%,#7a8ea6)}
.eyebrow{font-size:25px;color:#111}
.h2{font-size:45px;font-weight:700;color:var(--navy);white-space:nowrap}
.para{font-size:14.6px;line-height:24px;color:var(--text);text-align:justify}
/* works */
.works{left:0;top:1203px;width:1200px;height:584px;background:var(--band)}
.tools{left:720px;top:1203px;width:480px;height:630px;background:radial-gradient(circle at 45% 55%,#e04a3a 0,#2f6cc0 18%,#e0c23a 30%,rgba(201,207,219,0) 48%),linear-gradient(135deg,rgba(160,165,175,.6),rgba(201,207,219,0) 60%)}
.work-title{position:absolute;left:222px;font-size:26px;font-weight:500;color:#111}
.work-desc{position:absolute;left:222px;font-size:14.6px;line-height:23px;color:#333;width:320px}
/* services */
.card{position:absolute;width:224px;background:#fff;box-shadow:0 2px 8px rgba(0,0,0,.12);text-align:center;padding-top:78px}
.card h3{font-size:26px;font-weight:500;color:#111}
.card p{font-size:14.6px;line-height:24px;color:#444;margin:10px 26px 0}
.circ{position:absolute;width:104px;height:104px;border-radius:50%;background:var(--blue);display:flex;align-items:center;justify-content:center;box-shadow:0 0 0 3px #fff}
/* form */
.formband{left:0;top:2507px;width:598px;height:543px;background:var(--navy)}
.formphoto{left:598px;top:2507px;width:602px;height:543px;background:linear-gradient(120deg,#dfe4ea 0%,#c3ccd6 40%,#8a6a58 70%,#5a6068 100%)}
.formbox{left:112px;top:2571px;width:446px;height:418px;background:#fff}
.lbl{position:absolute;font-size:15px;font-weight:600;color:#111}
.fld{position:absolute;width:160px;border-bottom:1px solid #ddd;font-size:11px;color:#555;padding-bottom:4px}
.chk{position:absolute;font-size:11px;color:#444;display:flex;gap:6px;align-items:center}
.chk i{width:8px;height:8px;background:#ccc;display:block}
/* newsletter */
.news{left:112px;top:3241px;width:976px;height:209px;background:var(--navy)}
.input{left:179px;top:3302px;width:845px;height:89px;background:#fff;border-radius:45px;font-size:16px;color:#333;padding:36px 0 0 22px}
.sub{left:795px;top:3302px;width:229px;height:89px;background:var(--blue);border-radius:45px;color:#fff;font-size:20px;font-weight:600;display:flex;align-items:center;justify-content:center;box-shadow:-6px 0 0 var(--mid)}
/* footer */
.footer{left:0;top:3533px;width:1200px;height:404px;background:var(--black);color:#fff}
.fh{position:absolute;font-size:16px;font-weight:700;letter-spacing:.3px}
.fl{position:absolute;font-size:14px;line-height:26px}
.frow{position:absolute;display:flex;align-items:center;gap:10px;font-size:14px}
.frow .ico{width:32px;height:32px}
</style>
</head>
<body>

<header>
  <div class="abs brand" style="left:150px;top:56px">
    <i></i>Pelican HVAC
  </div>
  <div class="abs topbar">
    <span style="left:44px">Contact us via text or email</span>
    <span style="left:268px"><em class="ico"><svg width="14" height="14" viewBox="0 0 24 24"><path d="M6 2l4 4-2 3c1 3 4 6 7 7l3-2 4 4-3 4C10 22 2 14 2 5z" fill="none" stroke="#0054aa" stroke-width="2"/></svg></em>555-310-4827</span>
    <span style="left:448px"><em class="ico"><svg width="14" height="14" viewBox="0 0 24 24"><rect x="2" y="5" width="20" height="14" fill="none" stroke="#0054aa" stroke-width="2"/><path d="M2 5l10 8 10-8" fill="none" stroke="#0054aa" stroke-width="2"/></svg></em>hello@pelicanhvac.example</span>
  </div>
  <nav class="abs nav">
    <a style="left:0">Home</a><a style="left:76px">About Us</a><a style="left:177px">Who we are</a><a style="left:296px">What we do</a><a style="left:417px">Services</a><a style="left:509px">Contact Us</a>
  </nav>
</header>

<section>
  <div class="abs hero" role="img" aria-label="Technician in blue workwear servicing refrigeration compressors"></div>
  <div class="abs hero-tint"></div>
  <div class="abs welcome">Welcome To</div>
  <h1 class="hero" style="all:unset"></h1>
  <div class="abs" style="left:110px;top:318px;color:#fff;font-size:52px;font-weight:700;white-space:nowrap">PELICAN HVAC</div>
  <div class="btn" style="left:112px;top:407px;width:125px;height:34px">Get Started</div>
</section>

<section>
  <div class="abs frame"></div>
  <div class="abs frame2"></div>
  <div class="abs aboutphoto" role="img" aria-label="Engineer in hard hat operating a control panel"></div>
  <div class="abs eyebrow" style="left:645px;top:717px">About Us</div>
  <div class="abs h2" style="left:642px;top:757px">Who We Are</div>
  <p class="abs para" style="left:644px;top:829px;width:438px">Lorem ipsum dolor sit amet, consectetur adipiscing elit, sed do eiusmod tempor incididunt ut labore et dolore magna aliqua. Ut enim ad minim veniam, quis nostrud exercitation ullamco laboris nisi ut aliquip ex ea commodo consequat. Duis aute irure dolor in reprehenderit in voluptate velit esse cillum dolore eu fugiat nulla pariatur</p>
  <p class="abs para" style="left:644px;top:983px;width:444px">Sed ut perspiciatis unde omnis iste natus error sit voluptatem accusantium doloremque laudantium, totam rem aperiam, eaque ipsa quae ab illo inventore veritatis et quasi.</p>
  <div class="btn" style="left:644px;top:1074px;width:123px;height:38px">Read More</div>
</section>

<section>
  <div class="abs works"></div>
  <div class="abs tools" role="img" aria-label="Manifold gauges with coloured hoses and wrenches"></div>
  <div class="abs eyebrow" style="left:0;width:1200px;text-align:center;top:1234px">What We Do</div>
  <div class="abs h2" style="left:0;width:1195px;text-align:center;top:1270px">Explore Our Works</div>

  <svg class="abs" style="left:130px;top:1367px" width="56" height="48" viewBox="0 0 56 48" fill="none" stroke="#222" stroke-width="2"><rect x="2" y="2" width="52" height="16" rx="2"/><line x1="8" y1="10" x2="48" y2="10"/><circle cx="16" cy="34" r="10"/><circle cx="16" cy="34" r="3"/><path d="M34 26c4 4-4 8 0 14M42 26c4 4-4 8 0 14"/></svg>
  <div class="work-title" style="top:1362px">Air Conditioning</div>
  <div class="work-desc" style="top:1407px">Lorem ipsum dolor sit amet, consectetur adipiscing elit, sed do eiusmod</div>

  <svg class="abs" style="left:130px;top:1484px" width="52" height="66" viewBox="0 0 52 66" fill="none" stroke="#222" stroke-width="2"><path d="M26 2c4 14 22 20 22 40a22 22 0 0 1-44 0C4 30 14 24 14 14c6 6 6 10 6 14C26 20 28 12 26 2z"/><path d="M26 62c-8 0-10-8-8-14 2 4 6 4 6 0 0-6 6-8 6-14 4 8 8 12 6 20-1 5-5 8-10 8z"/></svg>
  <div class="work-title" style="top:1480px">Heating</div>
  <div class="work-desc" style="top:1525px">Lorem ipsum dolor sit amet, consectetur adipiscing elit, sed do eiusmod</div>

  <svg class="abs" style="left:126px;top:1600px" width="60" height="60" viewBox="0 0 60 60" fill="none" stroke="#222" stroke-width="2"><path d="M8 52L40 20M12 56L44 24M42 8a10 10 0 0 0 10 12l-6 6-10-10z"/><path d="M6 6l10 4 28 28 6 2 6 12-4 4-12-6-2-6L10 16z"/></svg>
  <div class="work-title" style="top:1593px">Maintenance</div>
  <div class="work-desc" style="top:1638px">Lorem ipsum dolor sit amet, consectetur adipiscing elit, sed do eiusmod</div>

  <div class="btn" style="left:538px;top:1721px;width:125px;height:34px">View More</div>
</section>

<section>
  <div class="abs eyebrow" style="left:0;width:1200px;text-align:center;top:1858px">Our Services</div>
  <div class="abs h2" style="left:0;width:1195px;text-align:center;top:1903px">Explore Our Reliable Services</div>

  <svg class="abs" style="left:40px;top:2000px" width="1040" height="110" viewBox="0 0 1040 110" fill="none" stroke="#5a3a1a" stroke-width="2" stroke-dasharray="3 4"><circle cx="12" cy="48" r="4" stroke-dasharray="none"/><path d="M16 50c20 8 30 12 56 20"/><path d="M210 42c60-10 90 0 120 52"/><path d="M480 40c60-20 100-10 135 26"/><path d="M820 94c40 0 60-30 100-36 20-4 30-20 40-30"/><path d="M990 14l22-8-8 22-5-9z" stroke-dasharray="none"/></svg>

  <div class="card" style="left:93px;top:2061px;height:224px"><h3>Lorem Ipsum</h3><p>Lorem ipsum dolor sit amet, consectetur adipiscing elit, sed do eiusmod</p></div>
  <div class="card" style="left:365px;top:2102px;height:226px"><h3>Lorem Ipsum</h3><p>Lorem ipsum dolor sit amet, consectetur adipiscing elit, sed do eiusmod</p></div>
  <div class="card" style="left:630px;top:2082px;height:223px"><h3>Lorem Ipsum</h3><p>Lorem ipsum dolor sit amet, consectetur adipiscing elit, sed do eiusmod</p></div>
  <div class="card" style="left:885px;top:2097px;height:227px"><h3>Lorem Ipsum</h3><p>Lorem ipsum dolor sit amet, consectetur adipiscing elit, sed do eiusmod</p></div>

  <div class="circ" style="left:148px;top:2010px"><svg width="48" height="44" viewBox="0 0 48 44" fill="none" stroke="#fff" stroke-width="2"><rect x="4" y="16" width="40" height="16" rx="2"/><line x1="10" y1="26" x2="38" y2="26"/><path d="M16 4v8M24 2v10M32 4v8M12 36v4M20 36v4M28 36v4M36 36v4"/></svg></div>
  <div class="circ" style="left:427px;top:2045px"><svg width="50" height="50" viewBox="0 0 50 50" fill="none" stroke="#fff" stroke-width="2"><circle cx="25" cy="25" r="14"/><circle cx="25" cy="25" r="6"/><path d="M25 4v6M25 40v6M4 25h6M40 25h6M10 10l4 4M36 36l4 4M40 10l-4 4M10 40l4-4"/></svg></div>
  <div class="circ" style="left:691px;top:2029px"><svg width="50" height="50" viewBox="0 0 50 50" fill="none" stroke="#fff" stroke-width="2"><path d="M14 22a11 11 0 0 1 22 0z"/><line x1="12" y1="22" x2="38" y2="22"/><path d="M12 46c0-10 6-14 13-14s13 4 13 14"/><path d="M6 8v22M44 12v16"/></svg></div>
  <div class="circ" style="left:946px;top:2038px"><svg width="50" height="50" viewBox="0 0 50 50" fill="none" stroke="#fff" stroke-width="2"><path d="M25 3l6 5 8-1 1 8 6 6-5 6 1 8-8 1-5 6-6-5-8 1-1-8-6-6 5-6-1-8 8-1z"/><line x1="18" y1="32" x2="32" y2="18"/><circle cx="19" cy="19" r="2.5"/><circle cx="31" cy="31" r="2.5"/></svg></div>

  <div class="btn" style="left:517px;top:2366px;width:166px;height:52px;border-radius:26px">Schedule Estimates</div>
</section>

<section>
  <div class="abs formband"></div>
  <div class="abs formphoto" role="img" aria-label="Technician in red cap servicing a wall-mounted air conditioner"></div>
  <div class="abs formbox">
    <div class="lbl" style="left:24px;top:36px">Name *</div>
    <div class="fld" style="left:24px;top:66px">First Name</div>
    <div class="fld" style="left:231px;top:66px">Last Name</div>
    <div class="lbl" style="left:24px;top:113px">Email *</div>
    <div class="fld" style="left:24px;top:143px">Email</div>
    <div class="lbl" style="left:231px;top:113px">Phone *</div>
    <div class="fld" style="left:231px;top:143px">Phone</div>
    <div class="lbl" style="left:24px;top:193px">Comments</div>
    <div class="fld" style="left:24px;top:222px">Message</div>
    <div class="lbl" style="left:231px;top:193px">Upload a Picture</div>
    <div class="fld" style="left:231px;top:222px;text-align:right;padding-right:16px"><svg width="12" height="11" viewBox="0 0 12 11" fill="none" stroke="#777"><rect x=".5" y=".5" width="11" height="10"/><path d="M1 9l3-4 3 3 2-2 2 3"/></svg></div>
    <div class="lbl" style="left:26px;top:267px">Join Our mailing list</div>
    <div class="chk" style="left:26px;top:295px"><i></i>Yes</div>
    <div class="chk" style="left:26px;top:317px"><i></i>No</div>
    <div class="abs" style="left:26px;top:358px;width:99px;height:32px;background:var(--navy);color:#fff;font-size:15px;font-weight:600;display:flex;align-items:center;justify-content:center">Submit</div>
  </div>
</section>

<section>
  <div class="abs h2" style="left:0;width:1195px;text-align:center;top:3142px">Subscribe To Our Newsletter</div>
  <div class="abs news"></div>
  <div class="abs input">Enter Your Email</div>
  <div class="abs sub">SUBSCRIBE</div>
</section>

<footer class="abs footer">
  <div class="abs brand" style="left:120px;top:118px;color:#fff;font-size:32px"><i></i>Pelican HVAC</div>
  <div class="fh" style="left:486px;top:106px">QUICK LINKS</div>
  <div class="fl" style="left:487px;top:142px">Home<br>About Us<br>Services<br>What we do<br>Contact Us</div>
  <div class="fh" style="left:660px;top:106px">HELP LINKS</div>
  <div class="fl" style="left:661px;top:142px">Privacy policy<br>Terms &amp; Conditions</div>
  <div class="fh" style="left:861px;top:106px">CONTACT US</div>
  <div class="frow" style="left:856px;top:146px"><em class="ico"><svg width="16" height="16" viewBox="0 0 24 24" fill="none" stroke="#555" stroke-width="2"><path d="M12 22s7-7 7-12a7 7 0 0 0-14 0c0 5 7 12 7 12z"/><circle cx="12" cy="10" r="2.5"/></svg></em>Lorem ipsum dolor sit amet</div>
  <div class="frow" style="left:856px;top:205px"><em class="ico"><svg width="16" height="16" viewBox="0 0 24 24"><path d="M6 2l4 4-2 3c1 3 4 6 7 7l3-2 4 4-3 4C10 22 2 14 2 5z" fill="none" stroke="#555" stroke-width="2"/></svg></em>555-310-4827</div>
  <div class="frow" style="left:856px;top:265px"><em class="ico"><svg width="16" height="16" viewBox="0 0 24 24"><rect x="2" y="5" width="20" height="14" fill="none" stroke="#555" stroke-width="2"/><path d="M2 5l10 8 10-8" fill="none" stroke="#555" stroke-width="2"/></svg></em>hello@pelicanhvac.example</div>
  <div class="abs" style="left:112px;top:332px;width:974px;height:1px;background:#666"></div>
  <div class="abs" style="left:0;width:1200px;text-align:center;top:353px;font-size:13.5px">Copyrights© PELICANHVAC.example 2024.All Rights reserved</div>
</footer>

</body>
</html>
```